International Travel Technology R&D business needs a wordpress website

We are a start up team of initially 2 individuals but plan to grow our team quickly, we have deep experience in travel technology. Our goal is to provide next generation technology research and development on behalf of our clients who are leading players in the travel technology industry. Attached our logos.

Target Market(s)

Travel Technology companies

Industry/Entity Type

Travel Industry

Coding

Coded - Design and coding required

Font styles to use
Sans Serif

Requirements
Must have
• Make use of our logo and colour scheme in the attached. Has to have a sense of adventure/ stepping into the unknown but equally must convey a sense of professionalism , we are a safe pair of hands. Sample themes are in the attachment .
Nice to have
• We have identified a theme on skinharbor which we feel would be inspirational. We hahe attached them to help in the design as inspiration.
Should not have
• images of airplanes , hotels etc, we want to project a future image.

```html
<!DOCTYPE html>
<html lang="en">
<head>
<meta charset="utf-8">
<title>Wayfront Labs</title>
<link href="https://fonts.googleapis.com/css2?family=Raleway:wght@500;600;700;800&family=Open+Sans:wght@400;600;700&display=swap" rel="stylesheet">
<style>
:root{
  --navy:#14246a;
  --navy-dark:#0f1d5a;
  --blue:#1f4fa0;
  --green:#5f9a36;
  --green-dark:#4e8a2b;
  --text:#555;
  --muted:#777;
  --white:#fff;
  --line:#e3e3e3;
}
*{box-sizing:border-box;margin:0;padding:0}
html,body{width:1200px;height:2308px;overflow:hidden}
body{font-family:"Open Sans",Arial,sans-serif;color:var(--text);background:var(--white);position:relative}
a{text-decoration:none}

/* header */
.site-header{position:absolute;top:0;left:0;width:1200px;height:122px;border-top:3px solid var(--navy)}
.brand{position:absolute;left:100px;top:44px;font-family:"Raleway",Arial,sans-serif;font-weight:700;font-size:32px;letter-spacing:3px;color:var(--navy);text-transform:uppercase}
.contact-item{position:absolute;top:40px;display:flex;gap:16px;align-items:flex-start}
.contact-item .label{font-size:16px;color:var(--navy);line-height:20px}
.contact-item .value{font-size:14px;color:var(--muted);line-height:22px}
.header-divider{position:absolute;left:883px;top:38px;width:1px;height:46px;background:var(--line)}

/* nav */
.main-nav{position:absolute;top:122px;left:0;width:1200px;height:52px;background:linear-gradient(var(--navy),var(--navy-dark))}
.main-nav a{position:absolute;top:0;height:52px;line-height:52px;font-size:13px;font-weight:700;color:var(--white);transform:translateX(-50%);text-transform:uppercase}
.main-nav a.active{left:100px;width:106px;text-align:center;background:var(--green);transform:none}

/* hero */
.hero{position:absolute;top:174px;left:0;width:1200px;height:514px;background:linear-gradient(90deg,#7a2f2a 0%,#c9a890 30%,#d9d4cc 55%,#b9bcbd 80%,#9ea3a6 100%)}
.hero-kicker{position:absolute;left:777px;top:216px;font-family:"Raleway",Arial,sans-serif;font-weight:800;font-size:29px;color:var(--white)}
.hero-title{position:absolute;left:777px;top:250px;font-family:"Raleway",Arial,sans-serif;font-weight:800;font-size:42px;color:var(--white);letter-spacing:1px}
.btn{display:inline-block;font-size:14px;color:var(--white);text-align:center;border-radius:2px;text-decoration:none}
.btn-green{background:linear-gradient(var(--green),var(--green-dark))}
.btn-navy{background:linear-gradient(#233a88,var(--navy))}
.hero .btn{position:absolute;left:777px;top:306px;width:157px;height:52px;line-height:52px}
.hero-arrow{position:absolute;top:230px}

/* section titles */
.section-title{position:absolute;left:0;width:1200px;text-align:center;font-family:"Raleway",Arial,sans-serif;font-weight:800;font-size:31px;color:var(--navy)}
.section-title span{color:var(--green)}
.title-rule{position:absolute;left:560px;width:80px;height:2px;background:var(--green)}

.welcome-text{position:absolute;left:160px;top:818px;width:886px;text-align:center;font-size:12.5px;line-height:24px;color:#555}
.welcome-actions{position:absolute;top:938px;left:443px;display:flex;gap:9px}
.welcome-actions .btn{width:157px;height:51px;line-height:51px}

/* services */
.services{position:absolute;top:1043px;left:0;width:1200px;height:449px;background:linear-gradient(90deg,#28468a 0%,#2e559c 37%,#7aa6c9 45%,#b9d3e6 70%,#7aa0c0 100%)}
.services-intro{position:absolute;left:0;top:0;width:454px;height:449px;background:rgba(30,70,150,.75)}
.services-title{position:absolute;left:100px;top:108px;font-family:"Raleway",Arial,sans-serif;font-weight:700;font-size:37px;line-height:46px;color:var(--white)}
.services-rule{position:absolute;left:100px;top:207px;width:250px;height:1px;background:rgba(255,255,255,.6)}
.services-lead{position:absolute;left:100px;top:222px;width:260px;font-size:12px;line-height:21px;color:#e6ecf7}
.services-panel{position:absolute;left:382px;top:65px;width:721px;height:320px;background:rgba(255,255,255,.9)}
.feature{position:absolute;width:270px}
.feature svg{position:absolute;left:-37px;top:-6px}
.feature h3{font-family:"Raleway",Arial,sans-serif;font-weight:700;font-size:13.5px;color:var(--green);text-transform:uppercase;margin-bottom:6px}
.feature p{font-size:12px;line-height:21px;color:#555}

/* blog */
.blog-card{position:absolute;top:1635px;width:315px}
.blog-thumb{width:315px;height:182px;border:4px solid #eee}
.blog-card h4{margin-top:20px;font-family:"Raleway",Arial,sans-serif;font-weight:700;font-size:16px;color:#333}
.byline{font-size:12px;color:var(--green);margin-top:6px}
.blog-card p{font-size:12px;line-height:21px;color:var(--muted);margin-top:6px}
.rating{display:flex;align-items:center;gap:10px;margin-top:10px;font-size:11px;color:var(--muted)}
.stars{color:#f2b01e;letter-spacing:1px;font-size:13px}
.stars b{color:#bbb;font-weight:400}
.rating .sep{width:1px;height:14px;background:#ccc}

/* footer */
.site-footer{position:absolute;top:2024px;left:0;width:1200px;height:284px;background:var(--navy)}
.footer-brand{position:absolute;left:100px;top:94px;font-family:"Raleway",Arial,sans-serif;font-weight:700;font-size:23px;letter-spacing:2px;color:var(--white);text-transform:uppercase}
.footer-col{position:absolute;top:37px;color:var(--white)}
.footer-col h5{font-family:"Raleway",Arial,sans-serif;font-weight:600;font-size:18px;text-transform:uppercase;margin-bottom:14px}
.footer-links{list-style:none;font-size:12.5px}
.footer-links li{height:23px}
.footer-links li::before{content:"›";margin-right:9px}
.footer-col p{font-size:12.5px;line-height:20px}
.email-field{margin-top:16px;width:263px;height:33px;background:var(--white);color:#888;font-size:12px;line-height:33px;padding-left:14px}
.footer-col .btn{margin-top:16px;width:102px;height:35px;line-height:35px;font-size:12.5px}
.contact-list{list-style:none;font-size:12.5px}
.contact-list li{display:flex;gap:14px;margin-bottom:12px;line-height:17px}
.contact-list svg{flex:none;margin-top:1px}
.copyright{position:absolute;left:100px;top:242px;font-size:12px;color:var(--white)}
.social{position:absolute;top:230px;left:984px;display:flex;gap:4px}
.social span{width:33px;height:33px;border-radius:50%}
</style>
</head>
<body>

<header class="site-header">
  <div class="brand">Wayfront Labs</div>
  <div class="contact-item" style="left:700px">
    <svg width="26" height="26" viewBox="0 0 24 24" fill="none" stroke="#888" stroke-width="1.5"><path d="M5 3h4l2 5-3 2a12 12 0 0 0 6 6l2-3 5 2v4a2 2 0 0 1-2 2A18 18 0 0 1 3 5a2 2 0 0 1 2-2z"/></svg>
    <div><div class="label">Contact us</div><div class="value">+ 555 0142 880</div></div>
  </div>
  <div class="header-divider"></div>
  <div class="contact-item" style="left:920px">
    <svg width="32" height="26" viewBox="0 0 32 24" fill="none" stroke="#888" stroke-width="1.6"><rect x="2" y="3" width="28" height="18" rx="2"/><path d="M2 4l14 10 14-10"/></svg>
    <div><div class="label">Email Us</div><div class="value">hello@wayfront.example</div></div>
  </div>
</header>

<nav class="main-nav">
  <a class="active" href="#">Home</a>
  <a href="#" style="left:280px">About us</a>
  <a href="#" style="left:410px">Services</a>
  <a href="#" style="left:554px">Destinations</a>
  <a href="#" style="left:690px">Tours</a>
  <a href="#" style="left:797px">Blog</a>
  <a href="#" style="left:905px">News</a>
  <a href="#" style="left:1032px">Contact us</a>
</nav>

<section class="hero" role="img" aria-label="Photo of a smiling young couple sharing earphones and a phone at a station platform">
  <svg class="hero-arrow" style="left:46px" width="16" height="60" viewBox="0 0 16 60"><path d="M14 2L2 30l12 28" fill="none" stroke="rgba(255,255,255,.7)" stroke-width="2"/></svg>
  <svg class="hero-arrow" style="left:1134px" width="16" height="60" viewBox="0 0 16 60"><path d="M2 2l12 28L2 58" fill="none" stroke="rgba(255,255,255,.7)" stroke-width="2"/></svg>
  <div class="hero-kicker">R&amp;D Company</div>
  <div class="hero-title">WAYFRONT</div>
  <a class="btn btn-green" href="#">View more info</a>
</section>

<h1 class="section-title" style="top:732px">WELCOME TO <span>WAYFRONT</span></h1>
<div class="title-rule" style="top:786px"></div>
<p class="welcome-text">Lorem Ipsum is simply dummy text of the printing and typesetting industry. Lorem Ipsum has been the industry's standard dummy text ever since the 1500s, when an unknown printer took a galley of type and scrambled it to make a type specimen book. It has survived not only five centuries, but also the leap into electronic typesetting, remaining essentially unchanged. It was popularised in the 1960s with the release of Lettersheet sheets containing Lorem Ipsum passages, and more recently with desktop publishing software like Pagecraft Studio including versions of Lorem Ipsum.</p>
<div class="welcome-actions">
  <a class="btn btn-navy" href="#">View more info</a>
  <a class="btn btn-green" href="#">Meet our team</a>
</div>

<section class="services" role="img" aria-label="Photo of a traveller relaxing in a deck chair on a sunny beach by the sea">
  <div class="services-intro"></div>
  <h2 class="services-title">OUR<br>SERVICES</h2>
  <div class="services-rule"></div>
  <p class="services-lead">Perspiciatis unde omnis iste natus error sit voluptatem accusantium doloremque laudan tium, totam rem aperiam, eaque ipsa quae ab illo inventore veritatis et</p>
  <div class="services-panel">
    <div class="feature" style="left:90px;top:65px">
      <svg width="30" height="36" viewBox="0 0 30 36" fill="none" stroke="#5f9a36" stroke-width="2"><rect x="3" y="5" width="20" height="27" rx="1"/><path d="M9 3h8v5H9z"/><path d="M8 15h10M8 20h10M8 25h6"/><circle cx="24" cy="28" r="5" fill="#5f9a36"/><path d="M21.5 28l2 2 3-3.5" stroke="#fff"/></svg>
      <h3>Superior Selection</h3>
      <p>Perspiciatis unde omnis iste natus error sit voluptatem accusantium doloremque laudan tium, totam rem aperiam</p>
    </div>
    <div class="feature" style="left:444px;top:65px">
      <svg width="34" height="34" viewBox="0 0 34 34" fill="none" stroke="#5f9a36" stroke-width="2.4"><path d="M29 11A14 14 0 1 0 31 17"/><path d="M30 4v7h-7"/><text x="17" y="22" text-anchor="middle" font-family="Raleway,sans-serif" font-weight="700" font-size="13" fill="#5f9a36" stroke="none">24</text></svg>
      <h3>24/7 Support</h3>
      <p>Perspiciatis unde omnis iste natus error sit voluptatem accusantium doloremque laudan tium, totam rem aperiam</p>
    </div>
    <div class="feature" style="left:90px;top:193px">
      <svg width="30" height="36" viewBox="0 0 30 36" fill="none" stroke="#5f9a36" stroke-width="2"><rect x="8" y="3" width="15" height="27" rx="2"/><path d="M13 26h5"/><path d="M4 22c0-4 3-6 6-6l3 2v9l-4 4H6z" fill="#5f9a36"/></svg>
      <h3>Anytime, Anywhere</h3>
      <p>Perspiciatis unde omnis iste natus error sit voluptatem accusantium doloremque laudan tium, totam rem aperiam</p>
    </div>
    <div class="feature" style="left:444px;top:193px">
      <svg width="32" height="32" viewBox="0 0 32 32"><circle cx="16" cy="16" r="14" fill="#5f9a36"/><path d="M9 9c3 1 5 3 4 6s-4 2-4 6M20 6c-1 3 2 4 4 5s1 5-2 6-2 5 0 7" fill="none" stroke="#fff" stroke-width="2"/></svg>
      <h3>World Best</h3>
      <p>Perspiciatis unde omnis iste natus error sit voluptatem accusantium doloremque laudan tium, totam rem aperiam</p>
    </div>
  </div>
</section>

<h2 class="section-title" style="top:1556px">LATEST <span>BLOG</span></h2>
<div class="title-rule" style="top:1604px"></div>

<article class="blog-card" style="left:97px">
  <div class="blog-thumb" role="img" aria-label="Photo of a couple laughing under an umbrella beside a yellow city tram" style="background:linear-gradient(135deg,#b9a57a,#8f8a86 50%,#c2392e)"></div>
  <h4>Perspiciatis unde omnis</h4>
  <div class="byline">by Mara on November 23, 2016</div>
  <p>Perspiciatis unde omnis iste natus error sit volup tatem accusantium doloremque laudantium, totam rem aperiam, eaque ipsa quae</p>
  <div class="rating"><span class="stars">★★★★<b>★</b></span><span class="sep"></span><span>👍 12 Reviews</span></div>
</article>
<article class="blog-card" style="left:443px">
  <div class="blog-thumb" role="img" aria-label="Photo of a couple sitting on a terrace by the sea at sunset" style="background:linear-gradient(180deg,#e8b15a,#e9c98f 45%,#6fa3c7)"></div>
  <h4>Perspiciatis unde omnis</h4>
  <div class="byline">by Mara on November 23, 2016</div>
  <p>Perspiciatis unde omnis iste natus error sit volup tatem accusantium doloremque laudantium, totam rem aperiam, eaque ipsa quae</p>
  <div class="rating"><span class="stars">★★★★<b>★</b></span><span class="sep"></span><span>👍 12 Reviews</span></div>
</article>
<article class="blog-card" style="left:788px">
  <div class="blog-thumb" role="img" aria-label="Photo of two tourists in sun hats holding a city map and pointing ahead" style="background:linear-gradient(135deg,#4d6b3e,#a7a195 50%,#e8e2d4)"></div>
  <h4>Perspiciatis unde omnis</h4>
  <div class="byline">by Mara on November 23, 2016</div>
  <p>Perspiciatis unde omnis iste natus error sit volup tatem accusantium doloremque laudantium, totam rem aperiam, eaque ipsa quae</p>
  <div class="rating"><span class="stars">★★★★<b>★</b></span><span class="sep"></span><span>👍 12 Reviews</span></div>
</article>

<footer class="site-footer">
  <div class="footer-brand">Wayfront Labs</div>
  <div class="footer-col" style="left:371px">
    <h5>Information</h5>
    <ul class="footer-links">
      <li>Home</li><li>About us</li><li>Services</li><li>Tours</li><li>Blog</li><li>Contact us</li>
    </ul>
  </div>
  <div class="footer-col" style="left:561px">
    <h5>Newsletter</h5>
    <p>Register Your email address to get<br>information about us</p>
    <div class="email-field">Email Address</div>
    <a class="btn btn-green" href="#">Subscribe</a>
  </div>
  <div class="footer-col" style="left:903px">
    <h5>Contact us</h5>
    <ul class="contact-list">
      <li><svg width="12" height="14" viewBox="0 0 12 16"><path d="M6 0a6 6 0 0 0-6 6c0 4 6 10 6 10s6-6 6-10a6 6 0 0 0-6-6zm0 8.5A2.5 2.5 0 1 1 6 3.5a2.5 2.5 0 0 1 0 5z" fill="#fff"/></svg><span>Northgate Office, 20417<br>Harbor Lane 58b.</span></li>
      <li style="margin-top:8px"><svg width="13" height="13" viewBox="0 0 24 24"><path d="M5 2h4l2 6-3 2a12 12 0 0 0 6 6l2-3 6 2v4a3 3 0 0 1-3 3A19 19 0 0 1 2 5a3 3 0 0 1 3-3z" fill="#fff"/></svg><span>1-555-310-4401</span></li>
      <li style="margin-top:14px"><svg width="14" height="13" viewBox="0 0 14 13"><rect x="0" y="3" width="14" height="10" rx="1" fill="#fff"/><rect x="3" y="0" width="8" height="4" fill="#fff"/><rect x="3" y="6" width="8" height="4" fill="#14246a"/></svg><span>1-555-310-4400</span></li>
      <li style="margin-top:14px"><svg width="14" height="11" viewBox="0 0 14 11"><rect width="14" height="11" rx="1" fill="#fff"/><path d="M0 1l7 5 7-5" fill="none" stroke="#14246a" stroke-width="1.4"/></svg><span>team@wayfront.example</span></li>
    </ul>
  </div>
  <div class="copyright">Copyrights ©&nbsp; Wayfront Labs 2016. All rights reserved. Terms and Conditions &nbsp;|&nbsp; Privacy Policy</div>
  <div class="social">
    <span style="background:#3b5bab"></span>
    <span style="background:#2ea3dc"></span>
    <span style="background:#d52222"></span>
  </div>
</footer>

</body>
</html>
```